San Francisco Leading Consulting firm - 47Vora Web Design Project

•Create a Web Design
•Uncoded webpage layout design
•2 Pages Design - Homepage + Interior Page

Task Description
Hello, we're looking for a re-design our current website www.47vora-example.com

we have a sample mockup design @

http://47vora.pubtrellis-example.org/

This shows the layout that we like and also a sample of 6 pictures that would change based on where you mouse over..

6 pictures HOME design needs to be included.

SMART
THOUGHTFUL
FLEXIBLE
CREATIVE SERVICES
TECHNICAL SERVICES
PARTNERS

sites we like:

http://www.melvanadvisory-example.com/Home.cfm?id=Home
http://www.plinthworks-example.com/index.html

Our company can be best described as: 100+ employees, cutting-edge, depandable, innovative, strong, smart.

Our Primary focus is: IT Consulting Services and Creative Design services

47Vora LLC is a consulting firm providing creative design, business and technology solutions to both private and public interests.

Established in 1996, 47Vora is a San Francisco based company providing specialists for a range of business needs including:

Creative Design Services
•Print
•Logo Design
•Website Design
•Illustration

and

Business and Technology solutions

•Application Software and Web Development
•Business Process Re-Design (BPR)
•Business/Systems Analysis and Requirement Documentation
•Mentoring and Training
•Network/Hardware Installation Services
•System Design and Architecture
•Vendor Management
•Docuvault Architecture and Implementation

our sample mockup site:

Reason: Due to holiday season, we're not available to work with designers and finilize our design.  

Thank you very much for submitting your design.

We appreciate your time and creativity.   Since, our office is currently closed for holidays, we will be reviewing it in details next week and will make our decision as soon as possible.

It would be great if you could submit any of your changes by Wed next week, so it would be part of our reviews. 

Please see updated wireframe under attachments:  we have some minor updates to our wireframe that we would like you to update your designs, if possible.  

We also encorouge you not to use our standard wireframe and come up with more unique designs.   Everything would be considered when we review your design.

 

Ardelle Market(s)

Creative services and professional services clients, including government agencies

Industry/Entity Type

Business

Requirements
Must have
• Clean, professional look, easy navigation

```html
<!DOCTYPE html>
<html lang="en">
<head>
<meta charset="utf-8">
<title>47Vora — Consulting, Creative &amp; Technical Services</title>
<link rel="stylesheet" href="https://fonts.googleapis.com/css2?family=Arimo:wght@400;700&family=Roboto+Condensed:wght@400;700&display=swap">
<style>
:root{
  --blue:#0a93cd;
  --blue-deep:#0479b3;
  --blue-light:#2bb3e6;
  --ink:#333;
  --ink-soft:#555;
  --grey:#8a8a8a;
  --rule:#d8d8d8;
  --white:#fff;
}
*{margin:0;padding:0;box-sizing:border-box}
html,body{width:1200px;height:960px;overflow:hidden;background:var(--white);font-family:"Arimo",Arial,sans-serif;color:var(--ink)}
.page{position:relative;width:1200px;height:960px}
.abs{position:absolute}

/* header */
.site-header{left:0;top:0;width:1200px;height:92px;border-bottom:2px solid var(--blue)}
.brand{left:170px;top:26px;display:flex;align-items:center;gap:10px}
.brand-dot{width:30px;height:30px;border-radius:50%;background:var(--blue)}
.brand-name{font-size:30px;font-weight:400;color:#444;letter-spacing:1px}
.main-nav{left:380px;top:37px;display:flex}
.main-nav a{font-size:12.5px;font-weight:700;color:var(--ink);text-decoration:none;padding:0 11px;border-left:1px solid var(--blue);line-height:18px}
.main-nav a:first-child{border-left:0}
.contact{left:929px;top:12px;font-size:12px;line-height:18px;color:#222}
.contact .hl{color:var(--blue);font-weight:700}

/* hero */
.hero{left:0;top:92px;width:1200px;height:528px;background:linear-gradient(180deg,#f0f0f0 0%,#c9c9c9 35%,#a8a8a8 70%,#8c8c8c 100%)}
.slider{left:118px;top:137px;width:960px;height:349px;background:linear-gradient(180deg,#0c9fd6,#0a8cc6);border-radius:3px 3px 0 0;overflow:hidden}
.slide-photo{position:absolute;left:460px;top:0;width:370px;height:349px;clip-path:polygon(0 0,100% 0,100% 100%,37px 100%);background:linear-gradient(135deg,#e7f1f6 0%,#c6dce6 45%,#8aa1ad 100%)}
.slide-band{position:absolute;left:0;top:195px;width:500px;height:154px;background:linear-gradient(180deg,rgba(255,255,255,.18),rgba(255,255,255,0))}
.slide-title{position:absolute;left:110px;top:92px;font-family:"Arimo",Arial,sans-serif;font-weight:700;font-size:50px;color:var(--white);letter-spacing:1px;text-shadow:1px 2px 3px rgba(0,0,0,.35)}
.slide-sub{position:absolute;left:110px;top:146px;font-family:"Roboto Condensed",Arial,sans-serif;font-size:23px;line-height:28px;color:var(--white);text-transform:uppercase;text-shadow:1px 1px 2px rgba(0,0,0,.35)}
.arrow{position:absolute;top:295px}
.slider-dots{left:118px;top:486px;width:960px;height:46px;background:rgba(255,255,255,.45);display:flex;justify-content:center;align-items:center;gap:13px;padding-left:6px}
.slider-dots span{width:15px;height:15px;border-radius:50%;background:#111}
.slider-dots span.active{background:var(--blue)}

/* clients */
.clients-title{left:126px;top:640px;font-size:20px;font-weight:700;line-height:24px;color:#222}
.clients-chevron{left:234px;top:644px}
.client-list{left:282px;top:640px;width:796px;height:50px;display:flex;align-items:center;justify-content:space-between}
.client{display:flex;align-items:center;gap:6px;font-size:16px;font-weight:700;color:#777}
.client i{display:block;width:12px;height:12px;border-radius:50%;background:#777}
.rule{left:120px;width:960px;height:1px;background:var(--rule)}

/* service tiles */
.tile{top:734px;width:280px;height:100px;border:1px solid #bbb;border-radius:4px;overflow:hidden;background:var(--white)}
.tile h2{position:absolute;left:6px;top:5px;font-size:15px;font-weight:400;color:#444}
.tile-art{position:absolute;border-radius:40% 40% 0 0}
.tile-corner{position:absolute;right:0;bottom:0}

/* footer */
.copyright{left:122px;top:874px;font-size:12px;color:#333}
.footer-nav{left:493px;top:874px;display:flex;gap:0}
.footer-nav a{font-size:12.5px;font-weight:700;color:var(--ink);text-decoration:none;padding:0 15px}
</style>
</head>
<body>
<div class="page">

  <header class="site-header abs">
    <div class="brand abs"><span class="brand-dot"></span><span class="brand-name">47VORA</span></div>
    <nav class="main-nav abs">
      <a href="#">Company</a><a href="#">Creative Services</a><a href="#">Technical Services</a><a href="#">Partners</a><a href="#">Contact Us</a>
    </nav>
    <address class="contact abs" style="font-style:normal">
      2285 Harlan Row, Ste 610<br>San Francisco, CA 94107<br>
      <span class="hl">415-555-0148</span><br><span class="hl">info@47vora-example.com</span>
    </address>
  </header>

  <section class="hero abs" role="img" aria-label="Black and white aerial view of the San Francisco skyline"></section>

  <div class="slider abs">
    <div class="slide-band"></div>
    <div class="slide-photo" role="img" aria-label="Photo of two business people shaking hands"></div>
    <div class="slide-title">PARTNERS</div>
    <div class="slide-sub">Together building a<br>successful relationship</div>
    <svg class="arrow" style="left:20px" width="30" height="52" viewBox="0 0 30 52"><polyline points="26,3 6,26 26,49" fill="none" stroke="#fff" stroke-width="7"/></svg>
    <svg class="arrow" style="left:912px" width="30" height="52" viewBox="0 0 30 52"><polyline points="4,3 24,26 4,49" fill="none" stroke="#fff" stroke-width="7"/></svg>
  </div>
  <div class="slider-dots abs"><span></span><span class="active"></span><span></span><span></span><span></span><span></span></div>

  <div class="clients-title abs">Featured<br>Clients</div>
  <svg class="clients-chevron abs" width="22" height="38" viewBox="0 0 22 38"><polyline points="4,3 17,19 4,35" fill="none" stroke="var(--blue)" stroke-width="6"/></svg>
  <div class="client-list abs">
    <span class="client"><i></i>Ardelle</span>
    <span class="client">Brisco</span>
    <span class="client">Calvex</span>
    <span class="client">Dornway</span>
    <span class="client">Elmtide</span>
    <span class="client">Fennick</span>
    <span class="client">Garrow</span>
    <span class="client">Halvern</span>
    <span class="client">Istria</span>
  </div>
  <div class="rule abs" style="top:707px"></div>

  <a class="tile abs" style="left:120px" href="#">
    <h2>Creative Services</h2>
    <div class="tile-art" style="left:80px;top:26px;width:148px;height:74px;background:linear-gradient(90deg,#f08ac8,#9b7de0,#6fd0f0,#f6e36a)" role="img" aria-label="Colourful flowing abstract illustration"></div>
    <svg class="tile-corner" width="42" height="42" viewBox="0 0 42 42"><polygon points="42,0 42,42 0,42" fill="var(--blue)"/><path d="M28 29h10M33 24v10" stroke="#fff" stroke-width="2"/></svg>
  </a>
  <a class="tile abs" style="left:458px" href="#">
    <h2>Business &amp; Technical Services</h2>
    <div class="tile-art" style="left:44px;top:28px;width:166px;height:72px;background:linear-gradient(180deg,#d8d8d8,#8d8d8d)" role="img" aria-label="Illustration of interlocking metal gears"></div>
    <svg class="tile-corner" width="42" height="42" viewBox="0 0 42 42"><polygon points="42,0 42,42 0,42" fill="var(--blue)"/><path d="M28 29h10M33 24v10" stroke="#fff" stroke-width="2"/></svg>
  </a>
  <a class="tile abs" style="left:793px" href="#">
    <h2>Partners</h2>
    <div class="tile-art" style="left:86px;top:8px;width:144px;height:74px;border-radius:8px;background:linear-gradient(90deg,#9ad3f0,#f3a6c8,#b8e08c,#f4cf7a)" role="img" aria-label="Colourful transit-style map of the United States"></div>
    <svg class="tile-corner" width="42" height="42" viewBox="0 0 42 42"><polygon points="42,0 42,42 0,42" fill="var(--blue)"/><path d="M28 29h10M33 24v10" stroke="#fff" stroke-width="2"/></svg>
  </a>

  <div class="rule abs" style="top:857px"></div>
  <footer>
    <p class="copyright abs">Copyright 2011, 47Vora, LLC All rights reserved.</p>
    <nav class="footer-nav abs">
      <a href="#">Home</a><a href="#">Company</a><a href="#">Technical Services</a><a href="#">Creative Services</a><a href="#">Partners</a><a href="#">Contact Us</a>
    </nav>
  </footer>
</div>
</body>
</html>
```